Velmarotix - world unique technology for better life - please let them know who am i at first sight

We need a new business card for company which is a provider of unique crystal based technology suitable for all living being. For more information and final design you can use our brochure (our colours are black and blue from brochure).
We use Verdana font

Industry/Entity Type

Business

Contact Information for Business Card

regular dimension

Font styles to use
Other font styles liked:
• Verdana

Requirements
Must have
• Logo
• name
• function/position
• phone
• mobile
• e-mail
• adress
Nice to have
• inovative design (technology directed)

```html
<!DOCTYPE html>
<html lang="en">
<head>
<meta charset="utf-8">
<title>Velmarotix – Business Card</title>
<link href="https://fonts.googleapis.com/css2?family=Exo+2:wght@400;500;600&family=Open+Sans:wght@400;600&display=swap" rel="stylesheet">
<style>
  :root {
    --page-bg: #e9ebee;
    --card-top: #ffffff;
    --card-mid: #eceef0;
    --brand-blue: #0aa3e0;
    --wave-gray: #b9bcbf;
    --ink: #1b1b1b;
    --divider: #ffffff;
  }
  * { margin: 0; padding: 0; box-sizing: border-box; }
  html, body { width: 1200px; height: 900px; overflow: hidden; background: var(--page-bg); }
  .canvas { position: relative; width: 1200px; height: 900px; }
  .card {
    position: absolute; left: 100px; top: 164px; width: 1000px; height: 572px;
    border-radius: 44px; overflow: hidden;
    background: radial-gradient(ellipse at 55% 35%, var(--card-top) 0%, var(--card-mid) 85%);
    box-shadow: 0 10px 30px rgba(0,0,0,.12);
    font-family: "Open Sans", Verdana, sans-serif; color: var(--ink);
  }
  .card-waves { position: absolute; inset: 0; width: 1000px; height: 572px; }
  .brand { position: absolute; left: 80px; top: 200px; display: flex; align-items: center; gap: 22px; }
  .brand-dot { width: 104px; height: 104px; border-radius: 50%; background: var(--brand-blue); }
  .brand-name {
    font-family: "Exo 2", Verdana, sans-serif; font-weight: 400; font-size: 66px;
    letter-spacing: 1px; color: var(--brand-blue);
  }
  .contact { position: absolute; right: 70px; top: 38px; text-align: right; }
  .person-name {
    font-family: "Exo 2", Verdana, sans-serif; font-weight: 600; font-size: 27px;
    letter-spacing: 1.5px; text-transform: uppercase; color: var(--brand-blue);
  }
  .person-role { font-size: 17px; font-weight: 600; margin-top: 2px; }
  .address { font-size: 18px; font-weight: 600; line-height: 26px; margin-top: 30px; }
  .lines { list-style: none; margin-top: 24px; font-size: 15px; line-height: 25px; }
  .lines li { display: flex; justify-content: flex-end; align-items: center; gap: 8px; }
  .lines svg { width: 16px; height: 16px; fill: var(--brand-blue); flex: none; }
</style>
</head>
<body>
<div class="canvas">
  <div class="card">
    <svg class="card-waves" viewBox="0 0 1000 572" aria-hidden="true">
      <path fill="var(--brand-blue)" d="M0,400 C200,470 450,480 650,430 C820,390 930,360 1000,318 L1000,572 L0,572 Z"/>
      <path fill="var(--wave-gray)" d="M0,458 C250,545 500,530 700,472 C850,428 950,394 1000,362 L1000,572 L0,572 Z"/>
      <path fill="none" stroke="var(--divider)" stroke-width="6" d="M0,458 C250,545 500,530 700,472 C850,428 950,394 1000,362"/>
    </svg>

    <div class="brand">
      <div class="brand-dot"></div>
      <div class="brand-name">VELMAROTIX</div>
    </div>

    <div class="contact">
      <div class="person-name">Marek Dolan</div>
      <div class="person-role">Managing Director</div>
      <div class="address">214 Crest Tower,<br>Harbor Lane KVT</div>
      <ul class="lines">
        <li>014 562 7380
          <svg viewBox="0 0 16 16"><path d="M3 1l3 3-1.5 2a9 9 0 0 0 5 5L11.5 9.5l3 3-2 2C6 14 2 10 1 3z"/></svg></li>
        <li>014 562 7380
          <svg viewBox="0 0 16 16"><path d="M4 0h8a1 1 0 0 1 1 1v14a1 1 0 0 1-1 1H4a1 1 0 0 1-1-1V1a1 1 0 0 1 1-1zm1 2v10h6V2zm3 11a1 1 0 1 0 0 2 1 1 0 0 0 0-2z"/></svg></li>
        <li>014 562 7380
          <svg viewBox="0 0 16 16"><path d="M4 1h6v4H4zM2 6h12v9H2zm2 2v2h3V8zm5 0v2h3V8z"/></svg></li>
        <li>marek@velmarotix.io
          <svg viewBox="0 0 16 16"><path d="M1 3h14v10H1zm1.5 1.5L8 9l5.5-4.5z" fill-rule="evenodd"/></svg></li>
        <li>www.velmarotix.io
          <svg viewBox="0 0 16 16"><path d="M8 0a8 8 0 1 0 0 16A8 8 0 0 0 8 0zm0 1.5c1 1.2 1.7 3.4 1.8 5.7H6.2C6.3 4.9 7 2.7 8 1.5zM1.6 7.2h3.1c.1-2 .6-3.8 1.4-5.1A6.5 6.5 0 0 0 1.6 7.2zm0 1.6a6.5 6.5 0 0 0 4.5 5.1c-.8-1.3-1.3-3.1-1.4-5.1zm4.6 0h3.6c-.1 2.3-.8 4.5-1.8 5.7-1-1.2-1.7-3.4-1.8-5.7zm5.1 0c-.1 2-.6 3.8-1.4 5.1a6.5 6.5 0 0 0 4.5-5.1zm3.1-1.6a6.5 6.5 0 0 0-4.5-5.1c.8 1.3 1.3 3.1 1.4 5.1z"/></svg></li>
      </ul>
    </div>
  </div>
</div>
</body>
</html>
```